Silver Bloom Marisol's Cleaning Service Business Cards Project

A business card with all contact details with logo design on there (already have a logo) eye catching Logo and contact info on one side, full logo on the back, must target upper class residential and corporate companies, fitness companies, still keep it on the feminine side of things , must look elegant

Target Market(s)

Upper class homes and corporate companies

Industry/Entity Type

Cleaning Service

Contact Information for Business Card

Name: Marisol Quenby
Position: Director
ABN: 31647209853
Email: marisolssilvercleaning@tidymail.example
Number: 0417906354

Font styles to use
Decorative

Colors

Designer to choose colors to be used in the design.

Requirements
Must have
• Available Sydney Wide, contact info and logo on one side, full logo on the back
Nice to have
• Professional appearance
Should not have
• Cheap advert looking stuff

```html
<!DOCTYPE html>
<html lang="en">
<head>
<meta charset="utf-8">
<title>Silver Bloom Marisol's Cleaning Service – Business Cards</title>
<link rel="stylesheet" href="https://fonts.googleapis.com/css2?family=Roboto:wght@400;500;700&display=swap">
<style>
  :root {
    --backdrop: #3a3a3c;
    --card-dark: #2d313d;
    --card-dark-edge: #262933;
    --aqua: #33e6dc;
    --aqua-soft: #5ef0e7;
    --white: #ffffff;
  }
  * { margin: 0; padding: 0; box-sizing: border-box; }
  html, body { width: 1200px; height: 960px; overflow: hidden; }
  body {
    background: var(--backdrop);
    font-family: "Roboto", Arial, sans-serif;
    position: relative;
  }
  .card {
    position: absolute;
    width: 600px;
    height: 342px;
    box-shadow: 0 3px 10px rgba(0,0,0,0.45);
  }
  .card-front { left: 320px; top: 108px; background: var(--card-dark); }
  .card-back { left: 320px; top: 493px; background: var(--aqua); }

  .front-brand {
    position: absolute;
    right: 26px;
    top: 40px;
    width: 200px;
    text-align: center;
    display: flex;
    flex-direction: column;
    align-items: center;
    gap: 14px;
  }
  .brand-dot {
    width: 42px; height: 42px;
    border-radius: 50%;
    border: 2px solid var(--aqua);
  }
  .brand-name {
    font-weight: 500;
    color: var(--aqua);
    font-size: 19px;
    line-height: 1.25;
    letter-spacing: 0.5px;
  }
  .identity {
    position: absolute;
    left: 0;
    top: 178px;
    padding-left: 32px;
  }
  .identity-bar {
    position: absolute;
    left: 0; top: 2px;
    width: 7px; height: 36px;
    background: var(--aqua);
  }
  .person-name {
    color: var(--aqua);
    font-weight: 500;
    font-size: 20px;
    letter-spacing: 0.2px;
  }
  .person-role {
    color: var(--aqua-soft);
    font-weight: 500;
    font-size: 15px;
    margin-top: 2px;
  }
  .abn {
    position: absolute;
    left: 32px; top: 234px;
    color: var(--white);
    font-size: 14px;
  }
  .contact-list {
    position: absolute;
    left: 32px; top: 262px;
    list-style: none;
    color: var(--white);
    font-size: 14px;
  }
  .contact-list li {
    display: flex;
    align-items: center;
    gap: 8px;
    height: 20px;
  }
  .contact-list svg { width: 13px; height: 13px; flex: none; }

  .back-brand {
    position: absolute;
    left: 0; right: 0; top: 86px;
    display: flex;
    flex-direction: column;
    align-items: center;
    gap: 22px;
  }
  .back-brand .brand-dot {
    width: 96px; height: 96px;
    border: 3px solid var(--white);
  }
  .back-brand .brand-name {
    color: var(--white);
    font-size: 28px;
  }
  .back-web {
    position: absolute;
    left: 0; right: 0; top: 290px;
    text-align: center;
    color: var(--white);
    font-size: 14px;
    letter-spacing: 4px;
  }
</style>
</head>
<body>
  <section class="card card-front">
    <div class="front-brand">
      <span class="brand-dot"></span>
      <span class="brand-name">Silver Bloom Marisol's Cleaning Service</span>
    </div>

    <div class="identity">
      <span class="identity-bar"></span>
      <h1 class="person-name">MARISOL QUENBY</h1>
      <p class="person-role">DIRECTOR</p>
    </div>

    <p class="abn">ABN: 31647209853</p>

    <ul class="contact-list">
      <li>
        <svg viewBox="0 0 16 16" aria-hidden="true"><path fill="#33e6dc" d="M3.6 1.2l2.3 2.6-1.2 1.8c.9 2 2.6 3.7 4.6 4.6l1.8-1.2 2.6 2.3-1.4 2.6C7 13.8 2.2 9 1 3.1z"/></svg>
        <span>0417906354</span>
      </li>
      <li>
        <svg viewBox="0 0 16 16" aria-hidden="true"><rect x="1" y="3" width="14" height="10" fill="#33e6dc"/><path d="M1 3.5l7 5 7-5" fill="none" stroke="#2d313d" stroke-width="1.4"/></svg>
        <span>marisolssilvercleaning@tidymail.example</span>
      </li>
      <li>
        <svg viewBox="0 0 16 16" aria-hidden="true"><circle cx="8" cy="8" r="7" fill="#33e6dc"/><path d="M1 8h14M8 1c-3 3.5-3 10.5 0 14M8 1c3 3.5 3 10.5 0 14" fill="none" stroke="#2d313d" stroke-width="1.2"/></svg>
        <span>www.silverbloom.example</span>
      </li>
    </ul>
  </section>

  <section class="card card-back">
    <div class="back-brand">
      <span class="brand-dot"></span>
      <span class="brand-name">Silver Bloom Marisol's Cleaning Service</span>
    </div>
    <p class="back-web">www.silverbloom.example</p>
  </section>
</body>
</html>
```